BOLD & MINIMALIST DESIGN NEEDED

We want a very bold but minimalistic business card design that is impactful and utilizes both sides of the business card. Our current logo is included for your use.

We want bold fonts and good use of negative space. We don't want the logo to overpower the design.

Target Market(s)

Professionals who are building new commercial buildings.

Industry/Entity Type

Construction

Contact Information for Business Card

Name, Title, email, office phone, cell phone, website

Font styles to use
Serif
Sans Serif

Requirements
Must have
• Bold design!

```html
<!DOCTYPE html>
<html lang="en">
<head>
<meta charset="utf-8">
<title>Ridgeline Design + Build — Business Card</title>
<link rel="stylesheet" href="https://fonts.googleapis.com/css2?family=Arimo:wght@400;700&display=swap">
<style>
  :root {
    --page-bg: #e6e4e1;
    --card-black: #0b0b0b;
    --brand-green: #4c9a2a;
    --ink-dark: #1b1b1b;
    --text-light: #d6d6d6;
    --text-muted: #b9b9b9;
    --frost-top: #eef3f8;
    --frost-mid: #f6f4f2;
    --frost-low: #ead6dc;
  }
  * { margin: 0; padding: 0; box-sizing: border-box; }
  html, body {
    width: 1200px;
    height: 970px;
    overflow: hidden;
    background: var(--page-bg);
    font-family: "Arimo", Arial, sans-serif;
  }
  .card {
    position: absolute;
    left: 60px;
    top: 177px;
    width: 1080px;
    height: 615px;
    overflow: hidden;
    box-shadow: 0 12px 40px rgba(0,0,0,0.25);
  }
  .card__surface {
    position: absolute;
    inset: 0;
    background: linear-gradient(175deg, var(--frost-top) 0%, var(--frost-mid) 55%, var(--frost-low) 85%, var(--frost-mid) 100%);
  }
  .card__shapes {
    position: absolute;
    inset: 0;
    width: 1080px;
    height: 615px;
  }
  .brand {
    position: absolute;
    left: 40px;
    top: 290px;
    width: 450px;
    display: flex;
    align-items: center;
    justify-content: center;
    gap: 16px;
  }
  .brand__mark {
    width: 26px;
    height: 26px;
    background: var(--brand-green);
    flex: none;
  }
  .brand__name {
    font-weight: 700;
    font-size: 40px;
    color: var(--ink-dark);
    letter-spacing: 1px;
    line-height: 1.1;
    text-transform: uppercase;
  }
  .contact {
    position: absolute;
    left: 645px;
    top: 124px;
    color: var(--text-light);
  }
  .contact__name {
    font-weight: 700;
    font-size: 35px;
    letter-spacing: 1px;
    color: var(--brand-green);
    text-transform: uppercase;
  }
  .contact__title {
    font-size: 25px;
    color: var(--text-muted);
    margin-top: 2px;
  }
  .contact__address {
    margin-top: 90px;
    font-size: 25px;
    line-height: 39px;
  }
  .contact__list {
    list-style: none;
    margin-top: 26px;
    font-size: 25px;
  }
  .contact__item {
    display: flex;
    align-items: center;
    gap: 18px;
    height: 37px;
  }
  .contact__icon {
    width: 28px;
    height: 28px;
    flex: none;
  }
</style>
</head>
<body>
  <div class="card">
    <div class="card__surface" role="img" aria-label="Frosted translucent card surface in soft white, blue and pink tones"></div>
    <svg class="card__shapes" viewBox="0 0 1080 615" aria-hidden="true">
      <path d="M553,134 C605,300 570,480 339,615 L640,615 L640,134 Z" fill="var(--brand-green)"/>
      <path d="M500,0 C615,120 640,420 420,615 L1080,615 L1080,0 Z" fill="var(--card-black)"/>
    </svg>

    <div class="brand">
      <span class="brand__mark"></span>
      <span class="brand__name">Ridgeline<br>Design + Build</span>
    </div>

    <div class="contact">
      <div class="contact__name">Owen Carter</div>
      <div class="contact__title">Manager</div>
      <div class="contact__address">PO BOX 418, Harbour Lane<br>7th street Geelong</div>
      <ul class="contact__list">
        <li class="contact__item">
          <svg class="contact__icon" viewBox="0 0 28 28"><circle cx="14" cy="14" r="14" fill="var(--brand-green)"/><path d="M10 7c1 0 2 3 2 4s-1.5 1.5-1 2.5 2.5 3.5 3.5 4 1.5-1 2.5-1 4 1 4 2-1.5 2.5-3 2.5c-4 0-10-6-10-10 0-2 1-4 2-4z" fill="var(--card-black)"/></svg>
          <span>555.204.7316</span>
        </li>
        <li class="contact__item">
          <svg class="contact__icon" viewBox="0 0 28 28"><circle cx="14" cy="14" r="14" fill="var(--brand-green)"/><rect x="7" y="9" width="14" height="10" rx="1" fill="var(--card-black)"/><path d="M7.5 9.5 L14 15 L20.5 9.5" stroke="var(--brand-green)" stroke-width="1.5" fill="none"/></svg>
          <span>hello@ridgelinebuild.com</span>
        </li>
        <li class="contact__item">
          <svg class="contact__icon" viewBox="0 0 28 28"><circle cx="14" cy="14" r="14" fill="var(--brand-green)"/><g fill="none" stroke="var(--card-black)" stroke-width="1.6"><circle cx="14" cy="14" r="7.5"/><ellipse cx="14" cy="14" rx="3.2" ry="7.5"/><path d="M6.5 14h15M8 10h12M8 18h12"/></g></svg>
          <span>www.ridgelinebuild.com</span>
        </li>
      </ul>
    </div>
  </div>
</body>
</html>
```